Supplement website needs three beautiful graphic elements

We need three elements designed for our new website. They should be bright, attractive, and colorful. Feel free to incorporate relevant stock images into the design. If you do so, please include a link to the original graphics.

I have included some graphics from a competitor's website that I really love. Use them as a general guideline. I don't want you to copy these, but your designs should be inspired by them. Please do not use the same fonts for all the designs.

Please note: the winning designer for this project will be selected to work on the remaining graphics for our website, around 5-8 more banners.

The 3 items needed are:

1) "Proudly Made in the USA at a NQB Approved cGMP Facility" (230x100)

2) "Diet Pill Advice - Which Brand Is Right For Me? Find Out Now!" (345x145)

3) "100% Satisfaction Guaranteed Or Your Money Back!" (230x100)

Please make sure to look through the graphics I uploaded.  I love their color schemes, the rounded corners and friendly feel.  Font choices are very thoughtfully done.  I also like how some graphics bleed off the inner borders.  All of this should be taken into consideration when you are creating the designs.

```html
<!DOCTYPE html>
<html lang="en">
<head>
<meta charset="utf-8">
<title>Diet Pill Advice – Website Banners</title>
<link rel="stylesheet" href="https://fonts.googleapis.com/css2?family=Nunito:wght@700;800;900&family=Archivo+Black&family=Roboto+Condensed:wght@400;700;900&family=Roboto:wght@400;500;700&display=swap">
<style>
  :root{
    --orange:#ee7a26;
    --teal:#2fb3c6;
    --green:#4f9a1c;
    --magenta:#d6267f;
    --navy:#1b3d8e;
    --blue:#2b5fb4;
    --border-blue:#2a5ca8;
    --usa-red:#a5141c;
    --ink:#222;
    --grey-text:#555;
    --white:#fff;
    --panel-grey:#e4e4e4;
    --gold:#f7a51c;
  }
  *{box-sizing:border-box;margin:0;padding:0}
  html,body{width:1200px;height:934px;overflow:hidden;background:var(--white)}
  .canvas{position:relative;width:1200px;height:934px;font-family:"Roboto",Arial,sans-serif}

  .headline{position:absolute;left:0;top:40px;width:1200px;text-align:center;
    font-family:"Nunito",Arial,sans-serif;font-weight:800;font-size:80px;line-height:1;letter-spacing:-1px}
  .headline .warm{color:var(--orange)}
  .headline .cool{color:var(--teal)}

  /* Advice banner */
  .advice{position:absolute;left:250px;top:135px;width:705px;height:205px;border:5px solid var(--orange);
    border-radius:22px;background:linear-gradient(#ffffff 0%,#f4f4f4 55%,#e2e2e2 100%);
    box-shadow:0 4px 8px rgba(0,0,0,.18)}
  .advice-photo{position:absolute;left:218px;top:126px;width:322px;height:218px;border-radius:16px 0 0 16px;
    background:linear-gradient(120deg,#6cc8bd 0%,#9fdcd3 45%,#eef0e4 100%)}
  .advice-copy{position:absolute;left:583px;top:150px;width:363px;text-align:center;font-family:"Nunito",Arial,sans-serif}
  .advice-copy .small{font-size:38px;font-weight:700;color:var(--green);line-height:1.1}
  .advice-copy .big{font-size:56px;font-weight:800;color:var(--green);line-height:1.05;letter-spacing:-1px}
  .advice-copy .cta{margin-top:14px;font-size:34px;font-weight:800;color:var(--magenta);text-align:right;padding-right:14px}

  /* USA badge, dark */
  .usa-dark{position:absolute;left:84px;top:407px;width:484px;height:209px;border-radius:16px;overflow:hidden;
    border:3px solid #cfd6e6;background:linear-gradient(160deg,var(--navy) 0%,var(--blue) 60%,#1b3d8e 100%);
    box-shadow:0 3px 7px rgba(0,0,0,.25)}
  .usa-dark .flag-band{position:absolute;left:0;bottom:0;width:100%;height:80px;
    background:linear-gradient(180deg,rgba(255,255,255,0) 0%,rgba(240,240,244,.9) 35%,#e8b3b6 70%,#d0343c 100%)}
  .usa-dark .lead{position:absolute;top:14px;width:100%;text-align:center;color:var(--white);font-size:28px;font-weight:500}
  .usa-dark .title{position:absolute;top:44px;width:100%;text-align:center;font-family:"Archivo Black",Arial,sans-serif;
    font-size:86px;line-height:1;color:var(--white);letter-spacing:-2px;
    text-shadow:-3px -3px 0 var(--navy),3px -3px 0 var(--navy),-3px 3px 0 var(--navy),3px 3px 0 var(--navy),0 5px 6px rgba(0,0,0,.4)}
  .usa-dark .strip{position:absolute;left:40px;top:155px;width:400px;height:34px;background:var(--white);
    border-radius:3px;text-align:center;font-size:21px;line-height:34px;color:var(--ink);font-weight:500}

  /* USA badge, light */
  .usa-light{position:absolute;left:609px;top:407px;width:484px;height:209px;border-radius:14px;
    border:4px solid var(--border-blue);background:linear-gradient(#ffffff,#f1f3f7);box-shadow:0 3px 7px rgba(0,0,0,.2)}
  .usa-light .copy{position:absolute;left:16px;top:14px;color:var(--grey-text);font-family:"Roboto Condensed",Arial,sans-serif}
  .usa-light .lead{font-size:28px;line-height:1.1;color:#444}
  .usa-light .title{font-weight:900;font-size:76px;line-height:.95;color:var(--usa-red);letter-spacing:-1px}
  .usa-light .foot{font-size:22px;line-height:1.25;color:#555}
  .usa-light .globe{position:absolute;left:300px;top:6px;width:176px;height:176px;border-radius:50%;
    background:radial-gradient(circle at 45% 40%,#6f9de6 0%,#2d5fb6 55%,#a9bce0 100%)}

  /* Guarantee badge */
  .guarantee{position:absolute;left:363px;top:660px;width:484px;height:213px;border-radius:14px;overflow:hidden;
    border:3px solid #cfcfcf;box-shadow:0 4px 8px rgba(0,0,0,.25)}
  .guarantee .top{position:absolute;left:0;top:0;width:100%;height:138px;
    background:linear-gradient(#ffd24a 0%,var(--gold) 45%,#f08a12 100%)}
  .guarantee .bottom{position:absolute;left:0;top:138px;width:100%;height:75px;
    background:linear-gradient(#ffffff 0%,var(--panel-grey) 100%);text-align:center;
    font-size:28px;font-weight:500;line-height:75px;color:var(--ink)}
  .guarantee .thumb{position:absolute;left:14px;top:10px;width:118px;height:118px;border-radius:50%;
    background:radial-gradient(circle at 50% 45%,#c0502a 0%,#8e1f14 70%,#6e150d 100%)}
  .guarantee .copy{position:absolute;left:150px;top:26px;font-family:"Roboto Condensed",Arial,sans-serif;color:#111}
  .guarantee .line1{font-size:36px;font-weight:700;line-height:1}
  .guarantee .line2{font-size:62px;font-weight:900;line-height:1;letter-spacing:-1px}
</style>
</head>
<body>
<div class="canvas">
  <h1 class="headline"><span class="warm">Diet Pill</span> <span class="cool">Advice</span></h1>

  <section class="advice"></section>
  <div class="advice-photo" role="img" aria-label="Photo of a measuring tape wrapped around a bottle of supplement capsules"></div>
  <div class="advice-copy">
    <div class="small">Which Brand Is</div>
    <div class="big">Right For Me?</div>
    <div class="cta">Find Out Now! &raquo;</div>
  </div>

  <section class="usa-dark">
    <div class="flag-band" role="img" aria-label="Waving American flag illustration"></div>
    <div class="lead">Proudly Made in</div>
    <div class="title">The USA</div>
    <div class="strip">at a NQB Approved cGMP Facility</div>
  </section>

  <section class="usa-light">
    <div class="copy">
      <div class="lead">Proudly Made in</div>
      <div class="title">The USA</div>
      <div class="foot">at a NQB Approved<br>cGMP Facility</div>
    </div>
    <div class="globe" role="img" aria-label="Glossy globe illustration in American flag colours"></div>
  </section>

  <section class="guarantee">
    <div class="top"></div>
    <div class="thumb" role="img" aria-label="Thumbs-up illustration in a round seal"></div>
    <div class="copy">
      <div class="line1">100% Satisfaction</div>
      <div class="line2">Guaranteed</div>
    </div>
    <div class="bottom">Or Your Money Back!</div>
  </section>
</div>
</body>
</html>
```